Velmarotix - world unique technology for better life - please let them know who am i at first sight

We need a new business card for company which is a provider of unique crystal based technology suitable for all living being. For more information and final design you can use our brochure (our colours are black and blue from brochure).
We use Verdana font

Industry/Entity Type

Business

Contact Information for Business Card

regular dimension

Font styles to use
Other font styles liked:
• Verdana

Requirements
Must have
• Logo
• name
• function/position
• phone
• mobile
• e-mail
• adress
Nice to have
• inovative design (technology directed)

```html
<!DOCTYPE html>
<html lang="en">
<head>
<meta charset="utf-8">
<title>Velmarotix Business Card</title>
<link rel="stylesheet" href="https://fonts.googleapis.com/css2?family=Open+Sans:wght@400;600;700&display=swap">
<style>
  :root {
    --bg: #e9e6df;
    --card-white: #fafafa;
    --card-grey: #e4e4e4;
    --ink-black: #0c0c0c;
    --brand-blue: #1ca3de;
    --silver: #c9ccd0;
    --text-dark: #2a2a2a;
    --text-light: #ffffff;
  }
  html, body {
    margin: 0;
    padding: 0;
    width: 1200px;
    height: 978px;
    overflow: hidden;
    background: var(--bg);
    font-family: "Open Sans", Verdana, sans-serif;
  }
  .canvas {
    position: relative;
    width: 1200px;
    height: 978px;
  }
  .card {
    position: absolute;
    left: 250px;
    width: 700px;
    height: 400px;
    border-radius: 26px;
    overflow: hidden;
    box-shadow: 0 10px 28px rgba(0,0,0,0.22);
  }

  /* Front side */
  .card-front {
    top: 60px;
    background: radial-gradient(circle at 50% 40%, var(--card-white) 0%, var(--card-grey) 100%);
    display: flex;
    flex-direction: column;
    align-items: center;
    justify-content: center;
  }
  .front-brand {
    display: flex;
    align-items: center;
    gap: 18px;
    margin-top: -10px;
  }
  .brand-dot {
    width: 30px;
    height: 30px;
    border-radius: 50%;
    background: var(--brand-blue);
  }
  .front-brand .brand-name {
    font-size: 52px;
    font-weight: 600;
    color: var(--brand-blue);
    letter-spacing: 1px;
  }
  .front-web {
    margin-top: 60px;
    font-size: 20px;
    font-weight: 700;
    letter-spacing: 2.5px;
    color: var(--text-dark);
  }

  /* Back side */
  .card-back {
    top: 510px;
    background: var(--brand-blue);
  }
  .back-shape {
    position: absolute;
    inset: 0;
    width: 700px;
    height: 400px;
  }
  .back-brand {
    position: absolute;
    left: 250px;
    top: 44px;
    display: flex;
    align-items: center;
    gap: 12px;
  }
  .back-brand .brand-dot {
    width: 22px;
    height: 22px;
  }
  .back-brand .brand-name {
    font-size: 40px;
    font-weight: 600;
    color: var(--brand-blue);
    letter-spacing: 1px;
  }
  .person {
    position: absolute;
    left: 286px;
    top: 136px;
  }
  .person-name {
    font-size: 22px;
    font-weight: 700;
    color: var(--brand-blue);
    margin: 0;
  }
  .person-role {
    font-size: 16px;
    color: var(--text-light);
    margin: 2px 0 0;
  }
  .contacts {
    position: absolute;
    left: 40px;
    top: 238px;
    color: var(--text-light);
    font-size: 14px;
    line-height: 1;
  }
  .contact-row {
    display: flex;
    gap: 22px;
    margin-bottom: 14px;
  }
  .contact-item {
    display: flex;
    align-items: center;
    gap: 7px;
  }
  .contact-item svg {
    width: 13px;
    height: 13px;
    fill: var(--text-light);
  }
  .address {
    font-size: 14px;
  }
</style>
</head>
<body>
<main class="canvas">

  <section class="card card-front" aria-label="Business card front">
    <div class="front-brand">
      <span class="brand-dot"></span>
      <span class="brand-name">Velmarotix</span>
    </div>
    <div class="front-web">www.velmarotix.cu</div>
  </section>

  <section class="card card-back" aria-label="Business card back">
    <svg class="back-shape" viewBox="0 0 700 400" aria-hidden="true">
      <path d="M0,0 H700 V400 H610 C520,300 330,150 0,118 Z" fill="var(--ink-black)"/>
      <path d="M0,118 C330,150 520,300 610,400" fill="none" stroke="var(--silver)" stroke-width="5"/>
    </svg>

    <div class="back-brand">
      <span class="brand-dot"></span>
      <span class="brand-name">Velmarotix</span>
    </div>

    <div class="person">
      <p class="person-name">Mirela Dovanic</p>
      <p class="person-role">Founder and CEO</p>
    </div>

    <div class="contacts">
      <div class="contact-row">
        <span class="contact-item">
          <svg viewBox="0 0 16 16"><path d="M3 1h3l1.5 4-2 1.3a9 9 0 0 0 4.2 4.2L11 8.5l4 1.5v3a2 2 0 0 1-2 2A12 12 0 0 1 1 3a2 2 0 0 1 2-2z"/></svg>
          014-278-5390
        </span>
        <span class="contact-item">
          <svg viewBox="0 0 16 16"><path d="M4 0h8a1 1 0 0 1 1 1v14a1 1 0 0 1-1 1H4a1 1 0 0 1-1-1V1a1 1 0 0 1 1-1zm1 2v10h6V2zm3 11a1 1 0 1 0 0 2 1 1 0 0 0 0-2z"/></svg>
          014-278-5390
        </span>
      </div>
      <div class="contact-row">
        <span class="contact-item">
          <svg viewBox="0 0 16 16"><path d="M1 3h14v10H1zm1.5 1.2V5l5.5 4 5.5-4v-.8zM2.5 6.6V12h11V6.6L8 10.6z"/></svg>
          info@velmarotix.com
        </span>
        <span class="contact-item">
          <svg viewBox="0 0 16 16"><path d="M8 0a8 8 0 1 0 0 16A8 8 0 0 0 8 0zm0 1.5c.9 0 2 1.9 2.3 5H5.7C6 3.4 7.1 1.5 8 1.5zM1.6 6.5a6.5 6.5 0 0 1 3.2-4.2A11 11 0 0 0 4.2 6.5zm0 3h2.6a11 11 0 0 0 .6 4.2 6.5 6.5 0 0 1-3.2-4.2zM8 14.5c-.9 0-2-1.9-2.3-5h4.6c-.3 3.1-1.4 5-2.3 5zm3.2-.8a11 11 0 0 0 .6-4.2h2.6a6.5 6.5 0 0 1-3.2 4.2zm.6-7.2a11 11 0 0 0-.6-4.2 6.5 6.5 0 0 1 3.2 4.2z"/></svg>
          www.velmarotix.cu
        </span>
      </div>
      <div class="address">Street Name, City Name, Zipcode-01234</div>
    </div>
  </section>

</main>
</body>
</html>
```